Business Card - connecting 2 souls and beggining the journey of self discovery

Logo on the front
with tag line

On the back list of services and contact details

Seminars
workshops
Coaching
podcasts

Darren Whitlow
Health & Wellbeing Life Coach
0491 372 615
darren@brightcoreliving.example
brightcoreliving.example

Industry/Entity Type

Life Coaching

Contact Information for Business Card

I like the use of colour from the logo to be used. I'm not a fan of white.

Requirements
Must have
• My tagline: The journey home starts with you
Nice to have
• Use of colour that is in the mind body soul logo

```html
<!DOCTYPE html>
<html lang="en">
<head>
<meta charset="utf-8">
<title>Brightcore Living – Business Card</title>
<link rel="stylesheet" href="https://fonts.googleapis.com/css2?family=Roboto:wght@400;500&family=Roboto+Condensed:wght@500;700&display=swap">
<style>
  :root {
    --backdrop: #2a2a2a;
    --card-front: #f3f3f3;
    --card-back: #7a7a7e;
    --ink-grey: #777777;
    --ink-dark: #4a4a4a;
    --accent-green: #58b585;
    --accent-coral: #ee5a6c;
    --mark-colour: #e9a23b;
    --divider: #b5b5b5;
    --white: #ffffff;
  }
  * { margin: 0; padding: 0; box-sizing: border-box; }
  html, body { width: 1200px; height: 960px; overflow: hidden; }
  body {
    background: var(--backdrop);
    font-family: "Roboto", Arial, sans-serif;
    position: relative;
  }
  .card {
    position: absolute;
    width: 600px;
    height: 342px;
    border-radius: 22px;
  }
  .card--front { left: 314px; top: 113px; background: var(--card-front); }
  .card--back  { left: 311px; top: 473px; background: var(--card-back); }

  .brand-mark {
    position: absolute;
    border-radius: 50%;
    background: var(--mark-colour);
  }
  .card--front .brand-mark { left: 115px; top: 98px; width: 78px; height: 78px; }
  .brand-name {
    position: absolute;
    font-family: "Roboto", Arial, sans-serif;
    font-weight: 400;
    white-space: nowrap;
  }
  .card--front .brand-name {
    left: 44px; top: 191px; width: 220px; text-align: center;
    font-size: 21px; color: var(--ink-grey); letter-spacing: -0.3px;
  }
  .tagline {
    position: absolute; left: 44px; top: 216px; width: 220px; text-align: center;
    font-size: 13px; font-weight: 500; color: var(--ink-grey); white-space: nowrap;
  }
  .divider {
    position: absolute; left: 285px; top: 100px; width: 1.5px; height: 142px;
    background: linear-gradient(to bottom, transparent, var(--divider) 20%, var(--divider) 80%, transparent);
  }
  .person-name {
    position: absolute; left: 306px; top: 110px;
    font-family: "Roboto Condensed", "Arial Narrow", sans-serif;
    font-weight: 700; font-size: 22px; color: var(--accent-green); text-transform: uppercase;
  }
  .person-role {
    position: absolute; left: 306px; top: 137px;
    font-family: "Roboto Condensed", "Arial Narrow", sans-serif;
    font-weight: 500; font-size: 16px; color: var(--accent-coral);
    text-transform: uppercase; letter-spacing: 0.2px;
  }
  .contact-list { position: absolute; left: 306px; top: 174px; list-style: none; }
  .contact-list li {
    display: flex; align-items: center; height: 19.5px;
    font-size: 14.5px; color: var(--ink-dark);
  }
  .contact-list svg { width: 13px; height: 13px; margin-right: 9px; fill: var(--accent-green); }

  .card--back .brand-mark { left: 247px; top: 91px; width: 108px; height: 108px; }
  .card--back .brand-name {
    left: 0; top: 220px; width: 600px; text-align: center;
    font-size: 29px; color: var(--white); letter-spacing: -0.5px;
  }
  .services {
    position: absolute; left: 0; top: 287px; width: 600px; text-align: center;
    font-size: 15px; color: var(--white); list-style: none;
  }
  .services li { display: inline; }
  .services li + li::before { content: "•"; font-size: 11px; margin: 0 5px 0 3px; }
</style>
</head>
<body>
  <section class="card card--front">
    <div class="brand-mark" aria-hidden="true"></div>
    <p class="brand-name">Brightcore Living</p>
    <p class="tagline">The journey home starts with you</p>
    <div class="divider"></div>
    <h1 class="person-name">Darren Whitlow</h1>
    <p class="person-role">Health &amp; Wellbeing Life Coach</p>
    <ul class="contact-list">
      <li><svg viewBox="0 0 24 24" aria-hidden="true"><path d="M6.6 10.8a15.1 15.1 0 0 0 6.6 6.6l2.2-2.2a1 1 0 0 1 1-.25 11.4 11.4 0 0 0 3.6.57 1 1 0 0 1 1 1V20a1 1 0 0 1-1 1A17 17 0 0 1 3 4a1 1 0 0 1 1-1h3.5a1 1 0 0 1 1 1c0 1.25.2 2.45.57 3.57a1 1 0 0 1-.25 1z"/></svg>0491 372 615</li>
      <li><svg viewBox="0 0 24 24" aria-hidden="true"><path d="M2 5h20v14H2z M2 5l10 7 10-7" stroke="#f3f3f3" stroke-width="1.5"/></svg>darren@brightcoreliving.example</li>
      <li><svg viewBox="0 0 24 24" aria-hidden="true"><circle cx="12" cy="12" r="10"/><path d="M2 12h20M12 2c3 3 3 17 0 20M12 2c-3 3-3 17 0 20" stroke="#f3f3f3" stroke-width="1.5" fill="none"/></svg>www.brightcoreliving.example</li>
    </ul>
  </section>

  <section class="card card--back">
    <div class="brand-mark" aria-hidden="true"></div>
    <p class="brand-name">Brightcore Living</p>
    <ul class="services">
      <li>Seminars</li><li>Workshops</li><li>Coaching</li><li>Podcasts</li>
    </ul>
  </section>
</body>
</html>
```